UI Redesign For Mobile Events iPhone App

We need a new UI design for our Social Events mobile app. Our app called Vessa is geared to help users find trending events in their local area. We show visual metrics on percent full and male female ratio and age group ratings. We want people to see whats going on at event before they get there through our app. Also we have a group chat portion to our app that we need included in the design. We would like to see a fresh, clean, and easy to use user interface that uses colors like, purple, blue and or hot pink.You may visit our website myvessa.example for more information about what our app is geared to do.
Updates

Target Market(s)

Our target market people that use social networks and attend social events ranging from ages 16-44.

Industry/Entity Type

Events

Requirements
Must have
• We would like to see an Example layout of all screens. (UPDATE: Please use our current background in your design, A PSD has been uploaded for you to grab the background. The Vessa Logo is NOT required to be included at the top of every screen)

-Profile Screen: Shows points earned, events attending, events created
-Event Listings Screen: Must have large image for event, visual metrics, date& time, location, attend button, invite friends button, Label for user who created the event
-Event Description Page: Shows everything as the event listing, has a description of the event, shows friends that are attending, points available
-Group Messaging Screen
-Slide Out Navigation Screen
-Notification Screen
-Ticket Screen
-Friends Activity Screen
-Friends Profile View: Shows events they've attended and points they've earned under their contact picture; invite button
-Sign-In Screen
-Register Screen

A way to label/categorize our different types of events:
-Nightlife
-Family
-Live Music & Concerts
-Restaurants
Group Chat Layout
Visual Meters for Percent Full, Male Female Ratio, Age Rating

```html
<!DOCTYPE html>
<html lang="en">
<head>
<meta charset="utf-8">
<title>Vessa – Edit Vessa and Side Menu</title>
<link rel="stylesheet" href="https://fonts.googleapis.com/css2?family=Lato:wght@300;400&display=swap">
<style>
  :root {
    --page-bg: #efe3e5;
    --page-bg-edge: #e6d6d9;
    --title-ink: #1a1a1a;
    --status-ink: #ffffff;
    --screen-top: #3a1a3a;
    --screen-bottom: #050205;
    --brand-blue: #0a66ff;
    --hot-pink: #e2104a;
    --panel-head: rgba(240, 228, 240, 0.9);
    --panel-line: rgba(255, 255, 255, 0.6);
    --ink-dark: #2a2a2a;
    --label-ink: #3c3540;
    --grid-purple: #5a1aa8;
    --avatar: #1f1f1f;
    --avatar-ring: #ffffff;
    --menu-bg: #1d0f22;
    --menu-active: #2f1b36;
    --menu-line: #2c1a31;
    --menu-ink: #e7e0ea;
  }
  * { box-sizing: border-box; margin: 0; padding: 0; }
  html, body { width: 1200px; height: 1000px; overflow: hidden; }
  body {
    position: relative;
    font-family: "Lato", "Helvetica Neue", Arial, sans-serif;
    background: radial-gradient(ellipse at 50% 45%, #f6eef0 0%, var(--page-bg) 55%, var(--page-bg-edge) 100%);
  }
  .showcase-title {
    position: absolute; top: 40px; width: 400px;
    font-size: 32px; font-weight: 400; color: var(--title-ink);
    text-align: center;
  }
  .showcase-title--left { left: 106px; }
  .showcase-title--right { left: 662px; }

  .screen {
    position: absolute; top: 240px; width: 332px; height: 587px;
    overflow: hidden; background: var(--screen-bottom);
  }
  .screen--edit { left: 148px; }
  .screen--menu { left: 696px; }

  .app-view {
    position: absolute; top: 0; width: 332px; height: 587px;
    background:
      radial-gradient(ellipse 70% 30% at 55% 8%, rgba(201,138,196,0.55), transparent 70%),
      radial-gradient(ellipse 60% 35% at 45% 45%, rgba(230,190,230,0.55), transparent 75%),
      linear-gradient(180deg, var(--screen-top) 0%, #6a2f68 20%, #8a4a86 42%, #4a1e48 70%, var(--screen-bottom) 92%);
  }
  .screen--edit .app-view { left: 0; }
  .screen--menu .app-view { left: 187px; box-shadow: -6px 0 12px rgba(0,0,0,0.5); }

  .status-bar {
    position: absolute; left: 0; top: 0; width: 332px; height: 22px; z-index: 5;
    display: flex; align-items: center; padding: 0 6px;
    font-size: 12px; color: var(--status-ink);
  }
  .status-bar .carrier { display: flex; align-items: center; gap: 4px; }
  .status-bar .time { position: absolute; left: 0; right: 0; text-align: center; }
  .status-bar .battery { margin-left: auto; display: flex; align-items: center; gap: 5px; }

  .menu-button { position: absolute; left: 12px; top: 42px; }
  .screen-title {
    position: absolute; left: 92px; top: 29px;
    font-size: 32px; font-weight: 300; color: #fff; white-space: nowrap;
  }

  .group-picker {
    position: absolute; left: 11px; top: 98px; width: 310px; height: 46px;
    background: var(--brand-blue); color: #fff;
    font-size: 18px; font-weight: 300;
    display: flex; align-items: center; justify-content: center;
  }
  .group-picker svg { position: absolute; right: 25px; top: 14px; }

  .friends-panel {
    position: absolute; left: 11px; top: 162px; width: 310px; height: 348px;
    background: linear-gradient(180deg, rgba(255,255,255,0.22) 0%, rgba(230,200,230,0.3) 40%, rgba(150,140,150,0.75) 80%, rgba(130,120,130,0.85) 100%);
  }
  .friends-panel__head {
    height: 44px; background: var(--panel-head);
    border-bottom: 1px solid var(--panel-line);
    position: relative; font-size: 14px; color: var(--ink-dark);
  }
  .friends-panel__label { position: absolute; left: 14px; top: 14px; letter-spacing: 0.3px; }
  .view-grid { position: absolute; left: 105px; top: 11px; }
  .view-list { position: absolute; left: 169px; top: 12px; }
  .add-friend {
    position: absolute; left: 236px; top: 11px;
    display: flex; align-items: center; gap: 6px;
    color: var(--brand-blue); font-size: 16px;
  }

  .friend {
    position: absolute; width: 80px; text-align: center;
    font-size: 13px; color: var(--label-ink);
  }
  .friend__avatar {
    width: 62px; height: 62px; margin: 0 auto 5px;
    border-radius: 50%; background: var(--avatar);
    border: 2px solid var(--avatar-ring);
  }
  .scroll-track {
    position: absolute; left: 290px; top: 60px; width: 2px; height: 273px;
    background: rgba(80, 40, 120, 0.45);
  }
  .scroll-thumb {
    position: absolute; left: 289px; top: 60px; width: 4px; height: 108px;
    background: var(--grid-purple);
  }

  .save-button {
    position: absolute; left: 11px; top: 530px; width: 310px; height: 45px;
    background: var(--hot-pink); color: #fff;
    font-size: 18px; font-weight: 300;
    display: flex; align-items: center; justify-content: center;
  }

  .side-menu {
    position: absolute; left: 0; top: 0; width: 187px; height: 587px;
    background: var(--menu-bg); z-index: 3; padding-top: 22px;
  }
  .side-menu__item {
    height: 58.5px; border-bottom: 1px solid var(--menu-line);
    display: flex; align-items: center; padding-left: 16px; gap: 18px;
    font-size: 15px; font-weight: 300; color: var(--menu-ink);
  }
  .side-menu__item--active { background: var(--menu-active); }
  .side-menu__item svg { width: 26px; flex: none; }
</style>
</head>
<body>

<h2 class="showcase-title showcase-title--left">My Vessa Screen</h2>
<h2 class="showcase-title showcase-title--right">Side Menu Bar</h2>

<section class="screen screen--edit">
  <div class="status-bar">
    <span class="carrier">
      <svg width="30" height="6" viewBox="0 0 30 6"><g fill="#fff"><circle cx="3" cy="3" r="2.6"/><circle cx="9" cy="3" r="2.6"/><circle cx="15" cy="3" r="2.6"/></g><g fill="none" stroke="#fff" stroke-width="0.8"><circle cx="21" cy="3" r="2.3"/><circle cx="27" cy="3" r="2.3"/></g></svg>
      WAVE
      <svg width="13" height="10" viewBox="0 0 13 10"><path d="M1 3.5a8 8 0 0 1 11 0M3 5.8a5 5 0 0 1 7 0M5 8a2 2 0 0 1 3 0" fill="none" stroke="#fff" stroke-width="1.3"/></svg>
    </span>
    <span class="time">4:21 PM</span>
    <span class="battery">
      100%
      <svg width="26" height="11" viewBox="0 0 26 11"><rect x="0.5" y="0.5" width="22" height="10" rx="2" fill="none" stroke="#fff"/><rect x="2" y="2" width="19" height="7" fill="#fff"/><rect x="23.5" y="3.5" width="2" height="4" fill="#fff"/></svg>
    </span>
  </div>

  <div class="app-view">
    <svg class="menu-button" width="27" height="19" viewBox="0 0 27 19"><g stroke="#fff" stroke-width="2"><line x1="0" y1="1" x2="27" y2="1"/><line x1="0" y1="9.5" x2="27" y2="9.5"/><line x1="0" y1="18" x2="27" y2="18"/></g></svg>
    <h1 class="screen-title">Edit Vessa</h1>

    <div class="group-picker">Sloths
      <svg width="18" height="18" viewBox="0 0 18 18"><circle cx="9" cy="9" r="9" fill="#fff"/><path d="M5 7.5l4 4 4-4" fill="none" stroke="#0a66ff" stroke-width="2.2"/></svg>
    </div>

    <div class="friends-panel">
      <div class="friends-panel__head">
        <span class="friends-panel__label">FRIENDS</span>
        <svg class="view-grid" width="22" height="22" viewBox="0 0 22 22"><g fill="#5a1aa8"><circle cx="3" cy="3" r="2.6"/><circle cx="11" cy="3" r="2.6"/><circle cx="19" cy="3" r="2.6"/><circle cx="3" cy="11" r="2.6"/><circle cx="11" cy="11" r="2.6"/><circle cx="19" cy="11" r="2.6"/><circle cx="3" cy="19" r="2.6"/><circle cx="11" cy="19" r="2.6"/><circle cx="19" cy="19" r="2.6"/></g></svg>
        <svg class="view-list" width="22" height="20" viewBox="0 0 22 20"><g stroke="#111" stroke-width="2"><line x1="0" y1="2" x2="22" y2="2"/><line x1="0" y1="7.5" x2="22" y2="7.5"/><line x1="0" y1="13" x2="22" y2="13"/><line x1="0" y1="18.5" x2="22" y2="18.5"/></g></svg>
        <span class="add-friend">
          <svg width="20" height="20" viewBox="0 0 20 20"><circle cx="10" cy="10" r="10" fill="#0a66ff"/><path d="M10 5v10M5 10h10" stroke="#fff" stroke-width="1.6"/></svg>Add
        </span>
      </div>

      <div class="friend" style="left:9px;top:62px"><div class="friend__avatar"></div>user1</div>
      <div class="friend" style="left:103px;top:62px"><div class="friend__avatar"></div>user1</div>
      <div class="friend" style="left:198px;top:62px"><div class="friend__avatar"></div>user3</div>
      <div class="friend" style="left:9px;top:154px"><div class="friend__avatar"></div>user4</div>
      <div class="friend" style="left:103px;top:154px"><div class="friend__avatar"></div>user5</div>
      <div class="friend" style="left:198px;top:154px"><div class="friend__avatar"></div>user6</div>
      <div class="friend" style="left:9px;top:247px"><div class="friend__avatar"></div>user7</div>
      <div class="friend" style="left:103px;top:247px"><div class="friend__avatar"></div>user8</div>
      <div class="friend" style="left:198px;top:247px"><div class="friend__avatar"></div>user9</div>

      <div class="scroll-track"></div>
      <div class="scroll-thumb"></div>
    </div>

    <div class="save-button">Save</div>
  </div>
</section>

<section class="screen screen--menu">
  <div class="status-bar">
    <span class="carrier">
      <svg width="30" height="6" viewBox="0 0 30 6"><g fill="#fff"><circle cx="3" cy="3" r="2.6"/><circle cx="9" cy="3" r="2.6"/><circle cx="15" cy="3" r="2.6"/></g><g fill="none" stroke="#fff" stroke-width="0.8"><circle cx="21" cy="3" r="2.3"/><circle cx="27" cy="3" r="2.3"/></g></svg>
      WAVE
      <svg width="13" height="10" viewBox="0 0 13 10"><path d="M1 3.5a8 8 0 0 1 11 0M3 5.8a5 5 0 0 1 7 0M5 8a2 2 0 0 1 3 0" fill="none" stroke="#fff" stroke-width="1.3"/></svg>
    </span>
    <span class="time">4:21 PM</span>
    <span class="battery">
      100%
      <svg width="26" height="11" viewBox="0 0 26 11"><rect x="0.5" y="0.5" width="22" height="10" rx="2" fill="none" stroke="#fff"/><rect x="2" y="2" width="19" height="7" fill="#fff"/><rect x="23.5" y="3.5" width="2" height="4" fill="#fff"/></svg>
    </span>
  </div>

  <nav class="side-menu">
    <div class="side-menu__item">
      <svg height="24" viewBox="0 0 26 24"><g fill="none" stroke="#e7e0ea" stroke-width="1.3"><circle cx="9" cy="6" r="4"/><path d="M1 22c0-5 3.5-8 8-8s8 3 8 8z"/><circle cx="18" cy="9" r="3.3"/><path d="M17 15.5c4.5-1 8 1.5 8 6h-6"/></g></svg>
      Profile
    </div>
    <div class="side-menu__item">
      <svg height="18" viewBox="0 0 26 18"><g fill="none" stroke="#e7e0ea" stroke-width="1.3"><rect x="1" y="1" width="24" height="16"/><path d="M1 1l12 9 12-9M1 17l9-8M25 17l-9-8"/></g></svg>
      Messages
    </div>
    <div class="side-menu__item">
      <svg height="26" viewBox="0 0 26 26"><g fill="none" stroke="#e7e0ea" stroke-width="1.3"><path d="M13 2c-5 0-7.5 4-7.5 8.5V16L3 20h20l-2.5-4v-5.5C20.5 6 18 2 13 2z"/><path d="M10.5 22.5a2.5 2.5 0 0 0 5 0"/></g></svg>
      Notifications
    </div>
    <div class="side-menu__item side-menu__item--active">
      <svg height="24" viewBox="0 0 26 24"><circle cx="13" cy="12" r="5" fill="none" stroke="#e7e0ea" stroke-width="1.3"/></svg>
      My Vessa
    </div>
    <div class="side-menu__item">
      <svg height="24" viewBox="0 0 26 24"><g fill="none" stroke="#e7e0ea" stroke-width="1.3"><path d="M14 2h9v9L11 23 2 14z"/><circle cx="18.5" cy="6.5" r="1.6"/></g></svg>
      Tickets
    </div>
    <div class="side-menu__item">
      <svg height="24" viewBox="0 0 26 24"><g fill="#e7e0ea"><circle cx="13" cy="3" r="2"/><circle cx="13" cy="21" r="2"/><circle cx="4" cy="12" r="2"/><circle cx="22" cy="12" r="2"/><circle cx="6.6" cy="5.6" r="2"/><circle cx="19.4" cy="5.6" r="2"/><circle cx="6.6" cy="18.4" r="2"/><circle cx="19.4" cy="18.4" r="2"/></g></svg>
      Events
    </div>
  </nav>

  <div class="app-view">
    <svg class="menu-button" width="27" height="19" viewBox="0 0 27 19"><g stroke="#fff" stroke-width="2"><line x1="0" y1="1" x2="27" y2="1"/><line x1="0" y1="9.5" x2="27" y2="9.5"/><line x1="0" y1="18" x2="27" y2="18"/></g></svg>
    <h1 class="screen-title">Edit Vessa</h1>

    <div class="group-picker">Sloths
      <svg width="18" height="18" viewBox="0 0 18 18"><circle cx="9" cy="9" r="9" fill="#fff"/><path d="M5 7.5l4 4 4-4" fill="none" stroke="#0a66ff" stroke-width="2.2"/></svg>
    </div>

    <div class="friends-panel">
      <div class="friends-panel__head">
        <span class="friends-panel__label">FRIENDS</span>
        <svg class="view-grid" width="22" height="22" viewBox="0 0 22 22"><g fill="#5a1aa8"><circle cx="3" cy="3" r="2.6"/><circle cx="11" cy="3" r="2.6"/><circle cx="19" cy="3" r="2.6"/><circle cx="3" cy="11" r="2.6"/><circle cx="11" cy="11" r="2.6"/><circle cx="19" cy="11" r="2.6"/><circle cx="3" cy="19" r="2.6"/><circle cx="11" cy="19" r="2.6"/><circle cx="19" cy="19" r="2.6"/></g></svg>
      </div>
      <div class="friend" style="left:9px;top:62px"><div class="friend__avatar"></div>user1</div>
      <div class="friend" style="left:103px;top:62px"><div class="friend__avatar"></div>user1</div>
      <div class="friend" style="left:9px;top:154px"><div class="friend__avatar"></div>user4</div>
      <div class="friend" style="left:103px;top:154px"><div class="friend__avatar"></div>user5</div>
      <div class="friend" style="left:9px;top:247px"><div class="friend__avatar"></div>user7</div>
      <div class="friend" style="left:103px;top:247px"><div class="friend__avatar"></div>user8</div>
    </div>

    <div class="save-button">Save</div>
  </div>
</section>

</body>
</html>
```